Unlock Your Way Upward Promotional Flyer

I Need a one page, one-sided 8.5 x 11 editable promotional flyer that POPS!, designed in photoshop

[TITLE]Unlock Your Way Upward: 3 BOLD Moves to Up-Level Your Business Now!

[CONTENT for the Flyer:]

At this content-rich event you will learn how to:
• Get out of feast and famine mode and into six, multi-six and/or seven figure-income mode
• Leapfrog your competition and become the obvious choice in your market
• Have your business aligned with who you are and what you want
• Enjoy your business far more than you imagined possible.
• Have more fun and time to yourself
• Live free and unbound!

Accolades
“Delphine helped us increase our six figure income by 41%...I feel reborn!” Marlene & Curtis Pettibone, Vienna, VA

“…Delphine is a joy to listen to - compelling, smart, provocative…” – Dennis Whitcombe, Charlotte, North Carolina

“Delphine helped me increase my business by 66%...without me spending more time, money, or making cold calls! …I am in the zone!” Kay Standish, Baltimore, MD
“Delphine is an energetic and dynamic speaker…content-rich…holds your attention to the very end!” Walt Pruitt, Frmr Pres., Hale & Brandt, MD, MD, D.C., PA, DE, NJ
“Delphine is the real estate whisperer!” Tom Garvey, Washington D.C.

“Delphine was prepared, funny, informative and made a connection with each of our agents…Fabulous!…even my admins were PUMPED!!! – Paul Denholm, New York

About Delphine:
Delphine is a highly regarded business development speaker & coach who knows how to pump up an audience and have them making more money, in less time, AND having more fun doing it! What’s not to love?! Consistently rated as an exceptional speaker and conference favorite! Among her work: Standing Apart: How to Draw Your Perfect Buyers Time After Time!, Finding Buyers Without Fuss, The Worst Outreach Errors Real Estate Agents Commit and How to Sidestep Them, Hard Seasons Build Hardy Brokers, Drive Within for Real Estate Agents.

[Also need a section for:]
Date: December 9, 2015, Time: 9:00 Am - 12:00 Noon, Place: Copper Lantern Convention, Ashford Mill, PA

Target Market(s)

Real Estate Agents

Industry/Entity Type

Real Estate Agent

Font styles to use
Sans Serif

Colors
0655a3
f37122

Requirements
Must have
• the top tier property mentor logo
Nice to have
• unlock your way upward logo; lots of POP! :-) ; open to other colors, accent colors.

```html
<!DOCTYPE html>
<html lang="en">
<head>
<meta charset="utf-8">
<title>Unlock Your Way Upward – Event Flyer</title>
<link href="https://fonts.googleapis.com/css2?family=Oswald:wght@500;700&family=Fira+Sans:wght@300;400;600&display=swap" rel="stylesheet">
<style>
  :root{
    --navy:#2b3990;
    --blue:#0655a3;
    --blue-dark:#0b3f7a;
    --orange:#f37122;
    --orange-light:#f89a2c;
    --gold:#f6a623;
    --yellow:#ffc83a;
    --ribbon-red:#8e1b10;
    --cream:#ffe6cc;
    --white:#ffffff;
    --grey:#8a8f96;
  }
  *{box-sizing:border-box;margin:0;padding:0}
  html,body{width:965px;height:1200px;overflow:hidden;background:#fff}
  .flyer{position:relative;width:965px;height:1200px;background:var(--white);font-family:"Fira Sans",sans-serif;overflow:hidden}
  .abs{position:absolute}

  .headline{left:0;width:965px;top:46px;text-align:center;font-family:"Oswald",sans-serif;font-weight:700;font-size:68px;letter-spacing:1px;color:var(--navy);line-height:1}
  .subhead{left:0;width:965px;top:141px;text-align:center;font-weight:600;font-size:33px;color:var(--gold);line-height:1}

  .band{left:0;top:0}

  .time-box{left:214px;top:222px;width:348px;height:50px;background:var(--navy);border-radius:8px 8px 0 0;color:#fff;font-family:"Oswald",sans-serif;font-weight:500;font-size:33px;text-align:center;line-height:50px}
  .time-box small{font-size:23px}
  .date-box{left:214px;top:271px;width:348px;height:64px;background:linear-gradient(var(--orange-light),var(--orange));border-radius:0 0 8px 8px;border:2px solid #fff;border-top:none;color:#fff;font-family:"Oswald",sans-serif;font-weight:700;font-size:37px;text-align:center;line-height:60px;letter-spacing:1px;box-shadow:0 3px 6px rgba(0,0,0,.35)}

  .learn-title{left:48px;top:356px;color:#fff;font-weight:600;font-size:23px;line-height:28px}
  .learn-list{left:48px;top:406px;width:500px;list-style:none;color:#fff;font-size:14.5px;line-height:18px;font-weight:400}
  .learn-list li{position:relative;padding-left:22px;margin-bottom:5px}
  .learn-list li::before{content:"";position:absolute;left:0;top:3px;width:12px;height:12px;border-radius:50%;background:radial-gradient(circle at 35% 35%,#fff3b0,var(--yellow) 55%,#e08a00)}

  .tagline{left:640px;top:278px;width:260px;text-align:center;color:var(--gold);font-weight:600;font-size:28px;line-height:37px}
  .place{left:595px;top:414px;width:350px;text-align:center;color:#fff;font-family:"Oswald",sans-serif;font-weight:500;font-size:26px;line-height:34px}

  .portrait{left:744px;top:536px;width:221px;height:219px;background:linear-gradient(160deg,#f0dcc8 0%,#c9a98c 45%,#2b2b2f 80%)}
  .speaker-name{left:500px;top:572px;width:260px;text-align:center;color:var(--grey);font-weight:600;font-size:28px;line-height:32px}
  .mentor-mark{left:490px;top:612px;width:270px;text-align:center;color:var(--orange);font-weight:600;font-size:32px;line-height:36px}

  .brand-mark{left:74px;top:652px;width:330px;display:flex;align-items:center;gap:12px;color:var(--blue-dark);font-weight:400;font-size:29px;line-height:34px}
  .brand-mark .dot{width:18px;height:18px;border-radius:50%;background:var(--orange);flex:none}

  .stripe{left:0;top:752px;width:965px;height:7px;background:linear-gradient(90deg,var(--yellow),var(--orange-light))}
  .bottom{left:0;top:759px;width:965px;height:441px;background:linear-gradient(135deg,var(--orange-light) 0%,var(--orange) 70%)}
  .divider{left:364px;top:782px;width:2px;height:330px;background:rgba(255,255,255,.25)}

  .section-title{color:#fff;font-weight:600;font-size:28px;line-height:34px}
  .about-title{left:49px;top:784px}
  .about-text{left:49px;top:834px;width:274px;color:var(--cream);font-size:14px;line-height:22.2px;text-align:justify;font-weight:400}

  .accolades-title{left:404px;top:786px}
  .quotes{left:404px;top:836px;width:524px;color:#fff;font-size:12.5px;line-height:16px;font-weight:300}
  .quote{padding-bottom:9px;margin-bottom:10px;border-bottom:1.5px solid rgba(255,255,255,.85)}
  .quote:last-child{border-bottom:none}
  .quote p{margin-bottom:8px}
  .quote p:last-child{margin-bottom:0}
  .quote p.inline{margin-bottom:5px}
  .quote .who{font-weight:600}
</style>
</head>
<body>
<main class="flyer">

  <h1 class="abs headline">UNLOCK YOUR WAY UPWARD</h1>
  <p class="abs subhead">3 BOLD MOVES TO UP-LEVEL YOUR BUSINESS NOW!</p>

  <svg class="abs band" width="965" height="760" viewBox="0 0 965 760" aria-hidden="true">
    <defs>
      <linearGradient id="bandFill" x1="0" y1="0" x2="1" y2="0">
        <stop offset="0" stop-color="#2a7cc6"/>
        <stop offset="0.45" stop-color="#0655a3"/>
        <stop offset="1" stop-color="#0b3f7a"/>
      </linearGradient>
    </defs>
    <polygon points="0,250 143,250 183,286 606,286 643,250 965,250 965,555 458,555 425,590 0,590"
             fill="url(#bandFill)"/>
    <path d="M183,286 L214,272 L214,300 Z" fill="var(--ribbon-red)"/>
    <path d="M562,272 L595,286 L562,300 Z" fill="var(--ribbon-red)"/>
  </svg>

  <div class="abs time-box">9:00 <small>AM</small> - 12:00 Noon</div>
  <div class="abs date-box">DECEMBER 9, 2015</div>

  <h2 class="abs learn-title">At this content-rich event you will learn how to:</h2>
  <ul class="abs learn-list">
    <li>Get out of feast and famine mode and into six, multi-six and/or seven figure-income mode</li>
    <li>Leapfrog your competition and become the obvious choice in your market</li>
    <li>Have your business aligned with who you are and what you want</li>
    <li>Enjoy your business far more than you imagined possible.</li>
    <li>Have more fun and time to yourself</li>
    <li>Live free and unbound!</li>
  </ul>

  <p class="abs tagline">“America’s Top Tier Property Mentor”™</p>
  <p class="abs place">Place:<br>Copper Lantern Convention,<br>Ashford Mill, PA</p>

  <div class="abs portrait" role="img" aria-label="Portrait photo of speaker Delphine Marsh"></div>
  <p class="abs speaker-name">Delphine Marsh</p>
  <p class="abs mentor-mark">TOP TIER<br>PROPERTY MENTOR</p>

  <div class="abs brand-mark"><span class="dot"></span>Unlock Your Way Upward</div>

  <div class="abs stripe"></div>
  <div class="abs bottom"></div>
  <div class="abs divider"></div>

  <h2 class="abs section-title about-title">About Delphine</h2>
  <p class="abs about-text">Delphine is a highly regarded business development speaker &amp; coach who knows how to pump up an audience and have them making more money, in less time, AND having more fun doing it! What’s not to love?! Consistently rated as an exceptional speaker and conference favorite! Among her work: Standing Apart: How to Draw Your Perfect Buyers Time After Time!, Finding Buyers Without Fuss, The Worst Outreach Errors Real Estate Agents Commit and How to Sidestep Them, Hard Seasons Build Hardy Brokers, Drive Within for Real Estate Agents.</p>

  <h2 class="abs section-title accolades-title">Accolades</h2>
  <div class="abs quotes">
    <div class="quote">
      <p>“Delphine helped us increase our six figure income by 41%...I feel reborn!”</p>
      <p class="who">Marlene &amp; Curtis Pettibone, Vienna, VA</p>
    </div>
    <div class="quote">
      <p>“Delphine is a joy to listen to - compelling, smart, provocative”</p>
      <p class="who">Dennis Whitcombe, Charlotte, North Carolina</p>
    </div>
    <div class="quote">
      <p class="inline">“Delphine helped me increase my business by 66%...without me spending more time, money, or making cold calls! ...I am in the zone!” Kay Standish, Baltimore, MD</p>
      <p class="inline">“Delphine is an energetic and dynamic speaker...content-rich...holds your attention to the very end!” Walt Pruitt, Frmr Pres., Hale &amp; Brandt, MD, MD, D.C., PA, DE, NJ</p>
      <p class="inline">“Delphine is the real estate whisperer!”</p>
      <p class="who">Tom Garvey, Washington D.C.</p>
    </div>
    <div class="quote">
      <p>“Delphine was prepared, funny, informative and made a connection with each of our agents...Fabulous!...even my admins were PUMPED!!!</p>
      <p class="who">Paul Denholm, New York</p>
    </div>
  </div>

</main>
</body>
</html>
```